need corporate, modern business card created for Consulting Company

I need a slick business card using elements from my website, as well as, integrating my pixelforge-created logo (see files).

The business card needs to be:
1. Corporate and modern
2. Clean and professional

I've included a PSD with the logo/icon that you can use to create it. Feel free to try a metallic finish on the logo, make it bigger/small, underlay it. Whatever you need to do to make my card stand out.

Try a black background, or white background or gray.

The idea is for my card to be memorable as well as professional and corporate.

Target Market(s)

Corporate business in the US and Canada.

Industry/Entity Type

Business

Contact Information for Business Card

Commerce Advancing Methods
Martin Coles, Senior Partner
office: 1 877 555 0143
mobile: 1 519 555 0172
website: http://www.brightvale.example

Requirements
Must have
• Card-related information
• corporate, yet modern
• clean and professional
• incorporate the icon only
• must have an editable form when complete!
Nice to have
• metallic icon might be cool
• try it with white or black

```html
<!DOCTYPE html>
<html lang="en">
<head>
<meta charset="utf-8">
<title>Brightvale Business Card</title>
<link href="https://fonts.googleapis.com/css2?family=Arimo:wght@400;700&display=swap" rel="stylesheet">
<style>
  :root {
    --stage: #e4e6e9;
    --paper: #f7f8f9;
    --paper-shade: #e9ebee;
    --blue-light: #5aa6dc;
    --blue: #3d8bd0;
    --blue-deep: #2a6fb6;
    --charcoal: #2b2d31;
    --ink: #2f3033;
    --white: #ffffff;
  }
  * { margin: 0; padding: 0; box-sizing: border-box; }
  html, body { width: 1200px; height: 885px; overflow: hidden; }
  body {
    background: var(--stage);
    font-family: "Arimo", Arial, sans-serif;
    display: flex;
    flex-direction: column;
    align-items: center;
    justify-content: center;
    gap: 40px;
  }
  .card {
    width: 700px;
    height: 400px;
    position: relative;
    overflow: hidden;
    background: linear-gradient(180deg, var(--white), var(--paper) 60%, var(--paper-shade));
    box-shadow: 0 6px 18px rgba(0,0,0,0.18);
  }

  /* Front */
  .front-brand {
    position: absolute; left: 0; top: 0; width: 100%; height: 150px;
    padding: 34px 0 0 90px;
  }
  .brand-lockup { display: flex; align-items: center; gap: 18px; }
  .brand-square {
    width: 38px; height: 38px; border-radius: 7px; background: var(--blue);
  }
  .brand-name {
    font-weight: 700; font-size: 62px; letter-spacing: -1px;
    color: var(--blue); line-height: 1;
  }
  .brand-tagline {
    margin: 8px 0 0 56px;
    font-size: 17px; color: var(--ink);
  }
  .front-band {
    position: absolute; left: 0; top: 150px; width: 100%; height: 190px;
    background: linear-gradient(90deg, var(--blue-light), var(--blue) 55%, var(--blue-deep));
    display: flex; align-items: center; justify-content: center; gap: 34px;
    color: var(--white);
  }
  .person { text-align: right; }
  .person-name { font-weight: 700; font-size: 24px; }
  .person-title { font-size: 17px; margin-top: 2px; }
  .person-web { font-size: 17px; margin-top: 26px; }
  .band-divider { width: 2px; height: 110px; background: rgba(255,255,255,0.8); }
  .contacts { list-style: none; font-size: 18px; }
  .contacts li { display: flex; align-items: center; gap: 10px; margin: 6px 0; }
  .contact-icon { width: 20px; height: 20px; flex: none; }
  .front-address {
    position: absolute; left: 0; bottom: 0; width: 100%; height: 60px;
    background: var(--charcoal); color: var(--white);
    display: flex; align-items: center; justify-content: center;
    font-size: 17px; letter-spacing: 0.2px;
  }

  /* Back */
  .back-name {
    position: absolute; left: 60px; bottom: 58px;
    display: flex; align-items: center; gap: 18px;
  }
  .back-name .brand-name { font-size: 76px; }
  .back-name .brand-square { width: 52px; height: 52px; border-radius: 10px; }
  .back-web {
    position: absolute; right: 56px; top: 70px;
    font-size: 24px; font-weight: 700; color: var(--blue-deep);
  }
</style>
</head>
<body>

  <section class="card card-front" aria-label="Business card front">
    <header class="front-brand">
      <div class="brand-lockup">
        <span class="brand-square"></span>
        <span class="brand-name">brightvale</span>
      </div>
      <p class="brand-tagline">Commerce Advancing Methods</p>
    </header>

    <div class="front-band">
      <div class="person">
        <p class="person-name">Martin Coles</p>
        <p class="person-title">Senior Partner</p>
        <p class="person-web">www.brightvale.example</p>
      </div>
      <span class="band-divider"></span>
      <ul class="contacts">
        <li>
          <svg class="contact-icon" viewBox="0 0 20 20" aria-hidden="true">
            <rect x="0" y="0" width="20" height="20" rx="4" fill="#fff"/>
            <path d="M6 4.5 L8 7 L7 8.5 Q8.5 11.5 11.5 13 L13 12 L15.5 14 L14 15.8 Q8 15 4.2 6 Z" fill="#3d8bd0"/>
          </svg>
          1 877 555 0143
        </li>
        <li>
          <svg class="contact-icon" viewBox="0 0 20 20" aria-hidden="true">
            <rect x="0" y="0" width="20" height="20" rx="4" fill="#fff"/>
            <rect x="6.5" y="3.5" width="7" height="13" rx="1.5" fill="#3d8bd0"/>
            <rect x="7.8" y="5" width="4.4" height="7.5" fill="#fff"/>
          </svg>
          1 519 555 0172
        </li>
        <li>
          <svg class="contact-icon" viewBox="0 0 20 20" aria-hidden="true">
            <rect x="0" y="0" width="20" height="20" rx="4" fill="#fff"/>
            <rect x="3.5" y="5.5" width="13" height="9" fill="none" stroke="#3d8bd0" stroke-width="1.6"/>
            <path d="M3.5 5.5 L10 11 L16.5 5.5" fill="none" stroke="#3d8bd0" stroke-width="1.6"/>
          </svg>
          info@brightvale.example
        </li>
      </ul>
    </div>

    <footer class="front-address">48 Harbour Lane West, Suite 1207, Kingsford, Ontario, K7A 2P5</footer>
  </section>

  <section class="card card-back" aria-label="Business card back">
    <p class="back-web">www.brightvale.example</p>
    <div class="back-name">
      <span class="brand-name">brightvale</span>
      <span class="brand-square"></span>
    </div>
  </section>

</body>
</html>
```